Change of trading name, rebrand

existing website to be updated with new theme and logo. existing website is
www.harlowbrentmere.com.au
Industry/Entity Type
Construction
Coding
Coded - Design and coding required
Number of Pages Required
5+ page
Requirements
Must have
- be mobile phone friendly

```html
<!DOCTYPE html>
<html lang="en">
<head>
<meta charset="utf-8">
<title>HBR Plant Hire</title>
<meta name="viewport" content="width=1200">
<link href="https://fonts.googleapis.com/css2?family=Michroma&family=Lato:wght@400;700&display=swap" rel="stylesheet">
<style>
:root{
  --navy:#28318f;
  --navy-deep:#1f2678;
  --ink:#1b1b1b;
  --text:#444;
  --white:#fff;
  --footer:#141414;
  --line:#e6e6e6;
}
*{box-sizing:border-box;margin:0;padding:0}
html,body{width:1200px;height:3962px;overflow:hidden}
body{font-family:'Lato',sans-serif;color:var(--text);background:var(--white);position:relative}
.display{font-family:'Michroma',sans-serif;font-variant:small-caps;letter-spacing:1px}

/* header */
.site-header{position:absolute;top:0;left:0;width:1200px;height:104px;background:var(--white);z-index:3}
.brand{position:absolute;left:95px;top:0;width:225px;height:147px;background:var(--white);display:flex;align-items:center;justify-content:center;gap:10px;box-shadow:0 2px 6px rgba(0,0,0,.08)}
.brand-mark{width:18px;height:18px;background:var(--navy)}
.brand-name{font-weight:700;font-size:26px;color:var(--navy);line-height:1}
.main-nav{position:absolute;left:366px;top:34px;display:flex;gap:30px;align-items:center;font-size:15px;color:#444}
.main-nav .active{background:var(--navy);color:#fff;padding:6px 11px;font-weight:700}
.call{position:absolute;left:928px;top:31px;display:flex;align-items:center;gap:18px}
.call-icon{width:37px;height:37px;background:var(--navy);display:flex;align-items:center;justify-content:center}
.call-text{font-size:14px;color:var(--navy);line-height:1.3}
.call-text strong{display:block;color:#333;font-size:17px;font-weight:400}

/* hero */
.hero{position:absolute;top:104px;left:0;width:1200px;height:600px;background:var(--navy)}
.hero-photo{position:absolute;right:0;top:0;width:730px;height:600px;clip-path:polygon(28% 0,100% 0,100% 100%,0 100%);background:linear-gradient(160deg,#7d8fae 0%,#c59a55 45%,#4d4436 100%)}
.hero-copy{position:absolute;left:111px;top:140px;width:370px;color:#fff}
.hero-copy .welcome{font-size:24px}
.hero-copy h1{font-size:47px;line-height:1.25;margin:14px 0 26px}
.hero-copy p{font-size:15px;line-height:1.75}
.btn-dark{display:inline-block;background:#0d0d0d;color:#fff;font-weight:700;font-size:16px;padding:12px 42px;margin-top:36px}
.arrow{position:absolute;top:280px;width:36px;height:36px;border-radius:50%;display:flex;align-items:center;justify-content:center}
.arrow.prev{left:33px;background:rgba(255,255,255,.5)}
.arrow.next{right:33px;background:#fff}

/* section titles */
.section-title{text-align:center}
.section-title h2{font-size:40px;color:var(--ink)}
.title-rule{display:flex;align-items:center;gap:10px;margin-top:14px}
.title-rule span{height:2px;width:42px;background:var(--navy)}
.title-rule i{width:6px;height:6px;background:var(--navy)}
.center .title-rule{justify-content:center}

.offer{position:absolute;top:780px;left:0;width:1200px}
.offer-grid{position:absolute;top:114px;left:111px;display:grid;grid-template-columns:repeat(3,302px);grid-auto-rows:236px;column-gap:34px;row-gap:35px}
.card{position:relative;display:flex;align-items:flex-end;justify-content:center;padding-bottom:36px;color:#fff;font-size:21px}
.card.a{background:linear-gradient(180deg,#8eb2d6,#b96a3b 60%,#5b5a52)}
.card.b{background:linear-gradient(180deg,#b59a56,#6d5a2f)}
.card.c{background:linear-gradient(180deg,#b8c5cf,#8a6b2a 60%,#4c4536)}
.card.d{background:linear-gradient(180deg,#8fb8e3,#9b8334 60%,#4f4a38)}
.card.e{background:linear-gradient(180deg,#7fb1e3,#3a3c3f 60%,#776140)}
.card.f{background:linear-gradient(180deg,#8a8c88,#7a6a3c 60%,#3b362c)}
.card.g{background:linear-gradient(180deg,#aac6de,#c8a534 55%,#4d4837)}
.card.h{background:linear-gradient(180deg,#7c9bc4,#4b5058 55%,#56503d)}
.card.featured{background:var(--navy);flex-direction:column;justify-content:flex-start;align-items:center;text-align:center;padding:32px 24px 0}
.card.featured h3{font-size:21px;font-weight:400}
.card.featured p{font-family:'Lato',sans-serif;font-size:14px;line-height:1.45;margin-top:14px;font-variant:normal;letter-spacing:0}
.card.featured a{font-family:'Lato',sans-serif;font-weight:700;font-size:14px;margin-top:14px;font-variant:normal;letter-spacing:0}

/* about */
.about-photo{position:absolute;left:111px;top:1763px;width:467px;height:605px;background:linear-gradient(180deg,#2e4d26 0%,#9aa3ae 40%,#d97a3a 70%,#3d3f45 100%)}
.about{position:absolute;left:678px;top:1778px;width:410px}
.about h2{font-size:40px;color:var(--ink)}
.about h4{color:var(--navy);font-size:20px;line-height:1.5;margin:42px 0 34px;font-weight:400}
.about p{font-size:14px;line-height:1.65;margin-bottom:20px}
.btn-navy{display:inline-block;background:var(--navy);color:#fff;font-weight:700;font-size:15px;padding:11px 42px;margin-top:22px}
.about-illus{position:absolute;left:848px;top:2270px;width:352px;height:205px;background:radial-gradient(ellipse at 55% 55%,#e2b52e 0%,#c9982a 45%,rgba(255,255,255,0) 72%)}

/* stats */
.stats{position:absolute;top:2505px;left:100px;width:1000px;display:flex;justify-content:space-between}
.stat{display:flex;flex-direction:column;align-items:center;text-align:center;font-size:21px;color:var(--ink);line-height:1.45}
.stat .badge{width:86px;height:86px;border-radius:50%;background:var(--navy);margin-bottom:23px;display:flex;align-items:center;justify-content:center}

/* partners */
.partners{position:absolute;top:2750px;left:-35px;display:flex;gap:23px}
.partner{width:161px;height:86px;background:#fff;box-shadow:0 1px 6px rgba(0,0,0,.15);display:flex;align-items:center;justify-content:center}
.partner span{width:92px;height:22px;border-radius:4px;background:#cdd0d8}
.partner.fade{opacity:.45}
.dots{position:absolute;top:2873px;left:571px;display:flex;gap:5px}
.dots i{width:9px;height:9px;border-radius:50%;background:#bbb}
.dots i:first-child{background:var(--navy)}

/* contact */
.contact{position:absolute;top:2960px;left:0;width:1200px;height:602px;background:var(--navy)}
.contact h2{position:absolute;left:113px;top:75px;font-size:35px;color:#fff}
.contact .title-rule{position:absolute;left:113px;top:125px}
.contact .title-rule span{background:#fff}.contact .title-rule i{background:#fff}
.form{position:absolute;left:113px;top:163px;width:425px}
.field{border:1px solid rgba(255,255,255,.7);height:47px;margin-bottom:14px;color:#fff;font-size:13px;padding:15px 13px}
.field.area{height:105px}
.submit{display:inline-block;background:#0d0d0d;color:#fff;font-weight:700;font-size:15px;padding:12px 52px;margin-top:0}
.map{position:absolute;left:638px;top:95px;width:457px;height:413px;background:linear-gradient(160deg,#e9efe6,#dfe8dc 50%,#d8e3ea)}

/* footer */
.site-footer{position:absolute;top:3562px;left:0;width:1200px;height:400px;background:var(--footer);color:#fff}
.footer-brand{position:absolute;left:113px;top:80px;display:flex;align-items:center;gap:12px}
.footer-brand .brand-mark{background:#fff;width:22px;height:22px}
.footer-brand span{font-size:34px;font-weight:700}
.footer-contact{position:absolute;left:113px;top:263px;font-size:15px;line-height:40px}
.footer-contact div{display:flex;align-items:center;gap:20px}
.footer-links{position:absolute;left:471px;top:100px}
.footer-links h3{font-size:21px;font-weight:700;font-family:'Lato',sans-serif}
.footer-links .underline{width:36px;height:2px;background:var(--navy);margin:8px 0 16px}
.link-cols{display:flex;gap:0}
.link-cols ul{list-style:none;font-size:14px;line-height:30px}
.link-cols ul:nth-child(1){width:236px}
.link-cols ul:nth-child(2){width:265px}
.copyright{position:absolute;top:370px;width:1200px;text-align:center;font-size:12px;left:0;margin-left:0}
</style>
</head>
<body>

<header class="site-header">
  <div class="brand"><i class="brand-mark"></i><span class="brand-name">HBR Plant Hire</span></div>
  <nav class="main-nav">
    <span class="active">Home</span><span>About Us</span><span>Plant Hire ⌄</span><span>Major Project Snapshot</span><span>More ⌄</span>
  </nav>
  <div class="call">
    <div class="call-icon"><svg width="16" height="16" viewBox="0 0 24 24"><path fill="#fff" d="M6.6 10.8a15 15 0 006.6 6.6l2.2-2.2c.3-.3.7-.4 1-.2 1.1.4 2.3.6 3.6.6.6 0 1 .4 1 1V20c0 .6-.4 1-1 1A17 17 0 013 4c0-.6.4-1 1-1h3.5c.6 0 1 .4 1 1 0 1.3.2 2.5.6 3.6.1.3 0 .7-.2 1z"/></svg></div>
    <div class="call-text">Call Us<strong>1300 462 915</strong></div>
  </div>
</header>

<section class="hero">
  <div class="hero-photo" role="img" aria-label="Yellow wheel loader lifting a bucket of earth at sunset"></div>
  <div class="hero-copy">
    <div class="welcome">Welcome to</div>
    <h1 class="display">HBR Plant Hire</h1>
    <p>Harlow Brentmere Resources Pty Ltd trading as HBR Heavy Equipment is a privately owned company that was established in 2010.</p>
    <span class="btn-dark">Get A Quote</span>
  </div>
  <div class="arrow prev"><svg width="14" height="14" viewBox="0 0 14 14"><path d="M9 2L4 7l5 5" stroke="#28318f" stroke-width="2" fill="none"/></svg></div>
  <div class="arrow next"><svg width="14" height="14" viewBox="0 0 14 14"><path d="M5 2l5 5-5 5" stroke="#333" stroke-width="2" fill="none"/></svg></div>
</section>

<section class="offer">
  <div class="section-title center">
    <h2 class="display">What Do We Offer</h2>
    <div class="title-rule"><span></span><i></i><span></span></div>
  </div>
  <div class="offer-grid">
    <div class="card a display" role="img" aria-label="Orange excavator on a work site">Excavators Hire</div>
    <div class="card b display" role="img" aria-label="Yellow dozer with blade">Dozers Hire</div>
    <div class="card c display" role="img" aria-label="Articulated dump truck">Dump Trucks Hire</div>
    <div class="card d display" role="img" aria-label="Yellow grader under blue sky">Graders Hire</div>
    <div class="card e display" role="img" aria-label="Loader beside large pipes">Loaders Hire</div>
    <div class="card f display" role="img" aria-label="Skid steer bobcat">Bobcats Hire</div>
    <div class="card g display" role="img" aria-label="Water cart truck">Water Carts Hire</div>
    <div class="card h display" role="img" aria-label="Backhoe loader">Backhoes Hire</div>
    <div class="card featured display">
      <h3>Compactors Hire</h3>
      <p>Compactors are a rare and specialist machine with specific application and we are proud to operate a fleet of Kestrel compactors for all your soil compaction needs.</p>
      <a>Read More ...</a>
    </div>
  </div>
</section>

<div class="about-photo" role="img" aria-label="Company owner standing beside an orange excavator attachment"></div>
<section class="about">
  <h2 class="display">About Us</h2>
  <div class="title-rule"><span></span><i></i><span></span></div>
  <h4>HBR Heavy Equipment Hire Committed to superior quality plant hire services.</h4>
  <p>Harlow Brentmere Heavy Equipment Hire specialise in the hire of heavy earthmoving, mining and construction machines with specialised attachments and tooling. Our array of machines and attachments is second to none, and we have one of the largest hire fleets available in South East Queensland.</p>
  <p>If its plant hire you require, then Harlow Brentmere Resources, or HBR as the local's call us – should be the first call you make. Wet or dry hire, we provide excellent operators and quality machines across all makes and models to guarantee you maximum up-time.</p>
  <span class="btn-navy">Get A Quote</span>
</section>
<div class="about-illus" role="img" aria-label="Yellow tracked excavator"></div>

<section class="stats">
  <div class="stat"><div class="badge"><svg width="40" height="40" viewBox="0 0 40 40" fill="none" stroke="#fff" stroke-width="2"><path d="M6 26a14 14 0 0128 0z"/><path d="M4 26h32v4H4z"/></svg></div>20+YEARS<br>OF EXPERIENCE</div>
  <div class="stat"><div class="badge"><svg width="40" height="40" viewBox="0 0 40 40" fill="none" stroke="#fff" stroke-width="2"><rect x="6" y="24" width="22" height="7"/><rect x="12" y="16" width="10" height="8"/><path d="M22 18l8-8 5 6"/></svg></div>100+MACHINES<br>IN FLEET</div>
  <div class="stat"><div class="badge"><svg width="40" height="40" viewBox="0 0 40 40" fill="none" stroke="#fff" stroke-width="2"><path d="M14 6l4 10 10 2 4 14H10l2-10z"/></svg></div>ONE OF QLD'S<br>LARGEST SUPPLIERS</div>
  <div class="stat"><div class="badge"><svg width="40" height="40" viewBox="0 0 40 40" fill="none" stroke="#fff" stroke-width="2"><circle cx="20" cy="14" r="6"/><path d="M8 34c0-8 6-12 12-12s12 4 12 12z"/></svg></div>ONSITE<br>SERVICING</div>
  <div class="stat"><div class="badge"><svg width="40" height="40" viewBox="0 0 40 40" fill="none" stroke="#fff" stroke-width="2"><path d="M12 6h16l-4 8h-8z"/><path d="M20 14v22M16 20h8M16 26h8"/></svg></div>CUSTOM MACHINE<br>ATTACHMENTS</div>
</section>

<section class="partners">
  <div class="partner fade"><span></span></div>
  <div class="partner"><span></span></div>
  <div class="partner"><span></span></div>
  <div class="partner"><span></span></div>
  <div class="partner"><span></span></div>
  <div class="partner"><span></span></div>
  <div class="partner fade"><span></span></div>
</section>
<div class="dots"><i></i><i></i><i></i><i></i></div>

<section class="contact">
  <h2 class="display">Contact us</h2>
  <div class="title-rule"><span></span><i></i><span></span></div>
  <form class="form">
    <div class="field">Name</div>
    <div class="field">Email Address</div>
    <div class="field">Phone</div>
    <div class="field area">Enquiry</div>
    <span class="submit">Submit</span>
  </form>
  <div class="map" role="img" aria-label="Street map showing the depot location"></div>
</section>

<footer class="site-footer">
  <div class="footer-brand"><i class="brand-mark"></i><span>HBR Plant Hire</span></div>
  <div class="footer-contact">
    <div><svg width="12" height="16" viewBox="0 0 12 16"><path fill="#fff" d="M6 0a6 6 0 00-6 6c0 4.5 6 10 6 10s6-5.5 6-10a6 6 0 00-6-6zm0 8.5A2.5 2.5 0 116 3.5a2.5 2.5 0 010 5z"/></svg>18 Ridgeline Rd, Coralvale QLD 4212</div>
    <div><svg width="14" height="14" viewBox="0 0 24 24"><path fill="#fff" d="M6.6 10.8a15 15 0 006.6 6.6l2.2-2.2c.3-.3.7-.4 1-.2 1.1.4 2.3.6 3.6.6.6 0 1 .4 1 1V20c0 .6-.4 1-1 1A17 17 0 013 4c0-.6.4-1 1-1h3.5c.6 0 1 .4 1 1 0 1.3.2 2.5.6 3.6.1.3 0 .7-.2 1z"/></svg>1300 462 915 , 07 3408 2176</div>
  </div>
  <div class="footer-links">
    <h3>Main Links</h3>
    <div class="underline"></div>
    <div class="link-cols">
      <ul><li>Home</li><li>About us</li><li>Machine Operator Jobs</li><li>Plant Hire</li><li>Attachments Hire</li><li>Policies</li></ul>
      <ul><li>Articulated Dump Trucks Hire</li><li>Dozer Hire</li><li>Excavator Diggers Hire</li><li>Grader Hire</li><li>Attachments Hire</li></ul>
      <ul><li>Backhoe Hire</li><li>Compactors Hire</li><li>Loader Hire</li><li>Skid Steer Hire</li><li>Water Cart Hire</li></ul>
    </div>
  </div>
  <div class="copyright">Copyright © 2024 HBR Plant Hire. All rights reserved.</div>
</footer>

</body>
</html>
```